Web Developer Needs a Business Card Design

I need a personal business card design that represents me as a web developer for potential employers. I would like the background to be a dark color on the front for contrast with my logo and name. The back will have all my information along with a smaller version of the logo. I want something with a modern look and feel, not too conservative. This will be used for potential employers and freelance work.

Industry/Entity Type

Business

Contact Information for Business Card

Front should have my logo and name. The back should have all my personal information which would include: name: Tom Varulek, phone: 570-614-3098, email: tomvarulek@quillbox.net, website url: www.tomvarulek.net, logo, web developer.

Font styles to use
Sans Serif

Requirements
Must have
• Must include my logo. The color palette base color will be the logo color.

```html
<!DOCTYPE html>
<html lang="en">
<head>
<meta charset="utf-8">
<title>Tom Varulek – Business Card</title>
<link rel="stylesheet" href="https://fonts.googleapis.com/css2?family=Open+Sans:wght@400;600;700&display=swap">
<style>
  :root {
    --teal: #6cc7b5;
    --teal-deep: #5db8a6;
    --teal-light: #8ad6c7;
    --ink: #1f1f1f;
    --paper: #ffffff;
    --backdrop: #eceae6;
  }
  * { box-sizing: border-box; margin: 0; padding: 0; }
  html, body {
    width: 1200px; height: 900px; overflow: hidden;
    background: var(--backdrop);
    font-family: "Open Sans", sans-serif;
  }
  .sheet {
    position: relative; width: 1200px; height: 900px;
    display: flex; align-items: center; justify-content: center; gap: 40px;
  }
  .card {
    position: relative; width: 540px; height: 309px; overflow: hidden;
    box-shadow: 0 6px 18px rgba(0,0,0,.18);
  }
  /* Front */
  .card--front { background: var(--teal); }
  .front-ring {
    position: absolute; left: -150px; top: 10px;
    width: 290px; height: 290px; border-radius: 50%;
    border: 3px solid var(--teal-deep);
    box-shadow: 1px 1px 0 var(--teal-light), inset 1px 1px 0 var(--teal-light);
  }
  .front-identity {
    position: absolute; right: 44px; top: 128px; text-align: right; color: var(--paper);
  }
  .front-name { font-size: 24px; font-weight: 700; letter-spacing: .5px; }
  .front-role { font-size: 14px; font-weight: 400; margin-top: 4px; }
  /* Back */
  .card--back { background: var(--paper); }
  .back-bands { position: absolute; inset: 0; }
  .back-mark {
    position: absolute; left: 82px; top: 58px;
    width: 100px; height: 100px; border-radius: 50%;
    background: var(--paper);
    display: flex; align-items: center; justify-content: center;
    color: var(--teal); font-size: 13px; font-weight: 700; text-align: center;
  }
  .back-identity { position: absolute; left: 236px; top: 150px; }
  .back-name { color: var(--teal); font-size: 22px; font-weight: 600; line-height: 1.1; }
  .back-role { color: var(--ink); font-size: 14px; margin-left: 10px; }
  .contact-list { list-style: none; margin-top: 22px; margin-left: 14px; }
  .contact-list li {
    display: flex; align-items: center; gap: 8px;
    color: var(--ink); font-size: 14px; line-height: 24px;
  }
  .contact-list svg { width: 12px; height: 12px; fill: var(--teal); flex: none; }
</style>
</head>
<body>
<main class="sheet">
  <section class="card card--front" aria-label="Card front">
    <div class="front-ring" aria-hidden="true"></div>
    <div class="front-identity">
      <h1 class="front-name">TOM VARULEK</h1>
      <p class="front-role">Front-End Developer</p>
    </div>
  </section>

  <section class="card card--back" aria-label="Card back">
    <svg class="back-bands" viewBox="0 0 540 309" preserveAspectRatio="none" aria-hidden="true">
      <polygon points="0,0 540,0 540,12 0,34" fill="var(--teal)"/>
      <polygon points="0,46 540,22 540,72 0,136" fill="var(--teal)"/>
    </svg>
    <div class="back-mark">Tom<br>Varulek</div>
    <div class="back-identity">
      <h2 class="back-name">Tom Varulek</h2>
      <p class="back-role">Front-End Developer</p>
      <ul class="contact-list">
        <li>
          <svg viewBox="0 0 24 24"><path d="M6.6 10.8a15 15 0 0 0 6.6 6.6l2.2-2.2c.3-.3.7-.4 1-.2 1.1.4 2.3.6 3.6.6.6 0 1 .4 1 1V20c0 .6-.4 1-1 1A17 17 0 0 1 3 4c0-.6.4-1 1-1h3.5c.6 0 1 .4 1 1 0 1.3.2 2.5.6 3.6.1.3 0 .7-.2 1z"/></svg>
          570-614-3098
        </li>
        <li>
          <svg viewBox="0 0 24 24"><path d="M2 5h20v14H2z M2 5l10 8 10-8" /></svg>
          tomvarulek@quillbox.net
        </li>
        <li>
          <svg viewBox="0 0 24 24"><path d="M10 14a4 4 0 0 1 0-5.6l3-3a4 4 0 0 1 5.6 5.6l-1.5 1.5-1.4-1.4 1.5-1.5a2 2 0 0 0-2.8-2.8l-3 3a2 2 0 0 0 0 2.8zm4-4a4 4 0 0 1 0 5.6l-3 3a4 4 0 0 1-5.6-5.6l1.5-1.5 1.4 1.4-1.5 1.5a2 2 0 0 0 2.8 2.8l3-3a2 2 0 0 0 0-2.8z"/></svg>
          www.tomvarulek.net
        </li>
      </ul>
    </div>
  </section>
</main>
</body>
</html>
```